Roofing Company Modern look

I want a modern and sophisticated look for our roofing business.

Our address is :

5217 Mallow Creek Ln
Orlando, Fl 32825

(407)-583-2196

www.HarborlineRoofsFl.com

I also want to make sure on the back there is a spot to put
Project Manager Name :

Number:

Because the cards will be used by all sales people

Project Manager Name :

Also there are accreditation we have logos are uploaded here as well that I would like maybe on the back of card as well

I also want to highlight our special attributions or trades:

Residential & Commercial
Fully Insured
License # CCC7482913
Insurance Claims
Serving Central Florida Since 1992
Free Estimates

Contact Information for Business Card

Our address is :

5217 Mallow Creek Ln
Orlando, Fl 32825

(407)-583-2196

Project Manager Name :

Residential & Commercial
Fully Insured
License # CCC7482913
Insurance Claims
Free Estimates

Font styles to use
Serif
Sans Serif

Colors
3176b5

Requirements
Must have
• Must have royal blue like my logo grey and black are the colors I like

```html
<!DOCTYPE html>
<html lang="en">
<head>
<meta charset="utf-8">
<title>Harborline Roofing &amp; Gutters – Business Card</title>
<link rel="stylesheet" href="https://fonts.googleapis.com/css2?family=Montserrat:wght@400;500;600;700&display=swap">
<style>
  :root {
    --page-bg: #e9e9ea;
    --card-white: #f6f6f6;
    --royal-blue: #3176b5;
    --blue-light: #42a4dc;
    --blue-deep: #1e63bd;
    --ink: #1c2233;
    --slate: #8a8a8f;
    --slate-faint: #9b9ba0;
    --white: #ffffff;
    --badge-red: #c8232c;
    --badge-navy: #2b3f7a;
  }
  * { box-sizing: border-box; margin: 0; padding: 0; }
  html, body { width: 1200px; height: 900px; overflow: hidden; }
  body {
    background: var(--page-bg);
    font-family: "Montserrat", sans-serif;
    position: relative;
  }
  .card {
    position: absolute;
    left: 250px;
    width: 700px;
    height: 400px;
    overflow: hidden;
    box-shadow: 0 6px 18px rgba(0,0,0,.18);
  }

  /* Back of card */
  .card-back { top: 35px; background: var(--slate); color: var(--white); }
  .rep { position: absolute; right: 44px; top: 36px; text-align: right; }
  .rep-name { font-size: 27px; font-weight: 600; letter-spacing: 1.5px; }
  .rep-title { font-size: 19px; font-weight: 400; margin-top: 2px; }
  .watermark-name {
    position: absolute; right: 40px; top: 160px; text-align: right;
    color: var(--slate-faint); font-weight: 600; text-transform: uppercase;
  }
  .watermark-name .main { font-size: 50px; letter-spacing: 5px; }
  .watermark-name .sub { font-size: 16px; letter-spacing: 4px; }
  .attributes {
    position: absolute; left: 48px; bottom: 40px;
    list-style: none; font-size: 19px; line-height: 1.45; font-weight: 500;
  }
  .attributes li::before { content: "• "; font-size: 13px; vertical-align: middle; }
  .badges {
    position: absolute; right: 40px; bottom: 40px;
    display: flex; align-items: center; gap: 14px;
  }

  /* Front of card */
  .card-front { top: 465px; background: var(--card-white); }
  .front-wave { position: absolute; inset: 0; }
  .brand {
    position: absolute; top: 92px; left: 0; right: 0;
    display: flex; flex-direction: column; align-items: center;
    color: var(--royal-blue); font-weight: 600; text-transform: uppercase;
  }
  .brand-mark { width: 34px; height: 34px; border-radius: 50%; background: var(--royal-blue); margin-bottom: 14px; }
  .brand-name { font-size: 58px; letter-spacing: 6px; line-height: 1; }
  .brand-sub { font-size: 17px; letter-spacing: 5px; margin-top: 8px; }
  .contact {
    position: absolute; display: flex; flex-direction: column; gap: 14px;
    color: var(--ink); font-size: 18px; font-weight: 500; letter-spacing: 1px;
  }
  .contact-left { left: 50px; bottom: 80px; }
  .contact-right { left: 440px; bottom: 52px; }
  .contact-row { display: flex; align-items: center; gap: 18px; }
  .icon {
    flex: none; width: 32px; height: 32px; border-radius: 50%;
    background: var(--ink); display: flex; align-items: center; justify-content: center;
  }
  .address { line-height: 1.25; }
</style>
</head>
<body>

<section class="card card-back" aria-label="Card back">
  <div class="rep">
    <div class="rep-name">PERSON NAME HERE</div>
    <div class="rep-title">Job Title</div>
  </div>

  <div class="watermark-name" aria-hidden="true">
    <div class="main">Harborline</div>
    <div class="sub">Roofing &amp; Gutters Inc.</div>
  </div>

  <ul class="attributes">
    <li>Residential &amp; Commercial</li>
    <li>Fully Insured</li>
    <li>License # CCC7482913</li>
    <li>Insurance Claims</li>
    <li>Serving Central Florida Since 1992</li>
    <li>Free Estimates</li>
  </ul>

  <div class="badges" role="img" aria-label="Accreditation badges">
    <svg width="46" height="34" viewBox="0 0 46 34"><rect x="1" y="1" width="44" height="32" rx="4" fill="var(--badge-navy)" stroke="#fff" stroke-width="2"/></svg>
    <svg width="150" height="38" viewBox="0 0 150 38"><rect x="1" y="1" width="148" height="36" fill="var(--badge-red)" stroke="#fff" stroke-width="2"/></svg>
    <svg width="52" height="52" viewBox="0 0 52 52"><circle cx="26" cy="26" r="24" fill="#f0f0f0" stroke="#5a5a5a" stroke-width="3"/></svg>
  </div>
</section>

<section class="card card-front" aria-label="Card front">
  <svg class="front-wave" width="700" height="400" viewBox="0 0 700 400" aria-hidden="true">
    <defs>
      <linearGradient id="band" x1="0" y1="0" x2="0" y2="1">
        <stop offset="0" stop-color="var(--blue-light)"/>
        <stop offset="1" stop-color="var(--blue-deep)"/>
      </linearGradient>
    </defs>
    <path d="M0 170 Q 260 290 700 270 L700 400 L0 400 Z" fill="url(#band)"/>
  </svg>

  <div class="brand">
    <div class="brand-mark"></div>
    <div class="brand-name">Harborline</div>
    <div class="brand-sub">Roofing &amp; Gutters Inc.</div>
  </div>

  <div class="contact contact-left">
    <div class="contact-row">
      <span class="icon"><svg width="16" height="16" viewBox="0 0 24 24"><path fill="#fff" d="M6.6 10.8a15.1 15.1 0 0 0 6.6 6.6l2.2-2.2a1 1 0 0 1 1-.25 11.4 11.4 0 0 0 3.6.57 1 1 0 0 1 1 1V20a1 1 0 0 1-1 1A17 17 0 0 1 3 4a1 1 0 0 1 1-1h3.5a1 1 0 0 1 1 1c0 1.25.2 2.45.57 3.57a1 1 0 0 1-.25 1z"/></svg></span>
      <span>(407)-583-2196</span>
    </div>
    <div class="contact-row">
      <span class="icon"><svg width="18" height="18" viewBox="0 0 24 24" fill="none" stroke="#fff" stroke-width="1.8"><circle cx="12" cy="12" r="9"/><path d="M3 12h18M12 3c3 3 3 15 0 18M12 3c-3 3-3 15 0 18"/></svg></span>
      <span>HarborlineRoofsFl.com</span>
    </div>
  </div>

  <div class="contact contact-right">
    <div class="contact-row">
      <span class="icon"><svg width="16" height="16" viewBox="0 0 24 24"><path fill="#fff" d="M12 3 2 12h3v8h5v-5h4v5h5v-8h3z"/></svg></span>
      <span class="address">5217 Mallow Creek Ln<br>Orlando, Fl 32825</span>
    </div>
  </div>
</section>

</body>
</html>
```